Bespoke Builders Business Card Design

We need a business card for an established builder of high quality bespoke homes in Auckland and Northland. We build and renovate homes collaboratively facilitating effective communication between owners, builders, architects, suppliers and tradespeople. We have never built or renovated a home that leaks or has faults. We only use reliable materials. We have never been sued or had legal action taken against us. We are honest builders of bespoke homes not group mass produced homes. Our niche market is in character homes. We practice sustainability and have built a lot of coastal property. We have been in business for over thirty years . We would like to see natural colors of the environment sand,sea and maybe vegetation . The design should communicate quality, sustainability,fair pricing, open communication and the originality of bespoke building. And the fact that the builder is registered.

Industry/Entity Type

Business

Contact Information for Business Card

Rowan Tellick Builders
Ph. 021583917
18 Kestrel Rd Harwood Bay Auckland 0814
PO Box 927 Mangawhai 0583

```html
<!DOCTYPE html>
<html lang="en">
<head>
<meta charset="utf-8">
<title>Rowan Tellick Builders – Business Card</title>
<link rel="stylesheet" href="https://fonts.googleapis.com/css2?family=Noto+Serif&family=PT+Sans&display=swap">
<style>
  :root {
    --backdrop: #e9e6e1;
    --card-edge: #8a3a1c;
    --card-face: #f1f1f0;
    --card-face-shade: #e4e4e3;
    --ink: #1c1c1c;
    --rule: #2a2a2a;
  }
  html, body {
    margin: 0;
    padding: 0;
    width: 1200px;
    height: 892px;
    overflow: hidden;
    background: var(--backdrop);
  }
  .canvas {
    width: 1200px;
    height: 892px;
    display: flex;
    align-items: center;
    justify-content: center;
  }
  .business-card {
    box-sizing: border-box;
    width: 900px;
    height: 514px;
    background: var(--card-edge);
    padding: 9px;
    box-shadow: 0 10px 30px rgba(0,0,0,0.18);
  }
  .card-face {
    width: 100%;
    height: 100%;
    background: radial-gradient(ellipse at 55% 45%, var(--card-face) 0%, var(--card-face) 55%, var(--card-face-shade) 100%);
    display: flex;
    flex-direction: column;
    align-items: center;
    justify-content: center;
    color: var(--ink);
  }
  .company-name {
    font-family: "Noto Serif", Georgia, serif;
    font-weight: 400;
    font-size: 54px;
    letter-spacing: 0.5px;
    margin: 0 0 30px;
  }
  .divider {
    width: 640px;
    height: 2px;
    background: var(--rule);
    margin: 0 0 30px;
  }
  .contact {
    font-family: "PT Sans", Arial, sans-serif;
    font-size: 24px;
    line-height: 1.3;
    text-align: center;
    margin: 0;
  }
  .contact-phone { margin-bottom: 22px; }
</style>
</head>
<body>
  <main class="canvas">
    <section class="business-card">
      <div class="card-face">
        <h1 class="company-name">Rowan Tellick Builders</h1>
        <div class="divider"></div>
        <p class="contact contact-phone">021583917</p>
        <p class="contact contact-address">18 Kestrel Rd Harwood Bay Auckland 0814</p>
        <p class="contact contact-postal">PO Box 927 Mangawhai 0583</p>
      </div>
    </section>
  </main>
</body>
</html>
```